I have a logo and need to design the business card and stationery.
Updates

The uploaded logo image named as GREYMARSH CONSTRUCTION which is to be replaced to GREYMARSH CONTRACTS. Kindly add below details and submit the designs- Company name- Greymarsh Engineering Contracts LLP Name & Post- Kelvan Joshi (Designated Partner) Address- Block No.317, Wing C, Tulvo Trade Court, Manek Pural Road, Ruparel Industrial Estate, Goregaon(E), Mumbai - 400 063 Contact- +91 97415 60382 Email- kelvanjoshi@mailbrook.example Website- www.greymarshcontracts.example Contact for Letterhead- +91-22-28754193

Hi Tovin Rahul, We are liking your Design #28860835. We have suggested some changes which are mentioned in feedback. Kindly revert with it asap to finalize this design.

Colors

Designer to choose colors to be used in the design.

```html
<!DOCTYPE html>
<html lang="en">
<head>
<meta charset="utf-8">
<title>Greymarsh Contracts – Stationery</title>
<link href="https://fonts.googleapis.com/css2?family=Lato:wght@400;700&display=swap" rel="stylesheet">
<style>
:root{
  --bg:#ececec;
  --paper:#ffffff;
  --ink:#111111;
  --grey:#555555;
  --rule:#666666;
  --faint:#f5f5f5;
  --band:#000000;
  --on-band:#ffffff;
}
*{margin:0;padding:0;box-sizing:border-box}
html,body{width:1200px;height:1200px;overflow:hidden;background:var(--bg);font-family:'Lato',sans-serif;color:var(--ink)}
.sheet,.card{position:absolute;background:var(--paper);box-shadow:0 2px 8px rgba(0,0,0,.25);overflow:hidden}
.icon{width:1em;height:1em;flex:none;fill:none;stroke:currentColor;stroke-width:2}
.icon.solid{fill:currentColor;stroke:none}

/* Letterhead */
.letterhead{left:23px;top:113px;width:756px;height:973px}
.letterhead .mark{position:absolute;left:110px;top:52px;width:79px;height:79px;background:var(--ink)}
.brand{position:absolute;font-weight:700;color:var(--ink);line-height:1;white-space:nowrap}
.letterhead .brand{left:56px;top:142px;font-size:23px}
.brand .line2{display:block;letter-spacing:.32em;font-size:.72em;margin-top:7px}
.letterhead .contact{position:absolute;left:457px;top:94px;border-left:2px solid var(--rule);padding-left:14px;font-size:15.5px;color:var(--grey);line-height:20.5px}
.contact li{list-style:none;display:flex;align-items:center;gap:8px}
.contact .icon{color:var(--ink);font-size:.85em}
.letterhead .watermark{position:absolute;left:174px;top:321px;width:408px;height:408px;background:var(--faint)}
.letterhead .footer{position:absolute;left:0;bottom:0;width:100%;height:76px;background:var(--band);color:var(--on-band);font-size:14.5px;line-height:24px;text-align:center;padding-top:14px}

/* Business card front */
.card{width:375px;height:217px}
.card-front{left:802px;top:368px}
.card-front .mark{position:absolute;left:31px;top:91px;width:36px;height:36px;background:var(--ink)}
.card-front .brand{left:73px;top:95px;font-size:13px}
.card-front .brand .line2{margin-top:4px}
.card-front .divider{position:absolute;left:188px;top:74px;width:1px;height:70px;background:var(--rule)}
.card-front .person{position:absolute;left:207px;top:71px}
.person .name{font-size:13.5px;font-weight:700;text-transform:uppercase;line-height:1}
.person .role{font-size:9.5px;color:var(--grey);margin-top:4px}
.card-front .contact{margin-top:12px;font-size:9.5px;color:var(--grey);line-height:13px}
.card-front .contact .icon{font-size:.9em}
.card-front .footer{position:absolute;left:0;bottom:0;width:100%;height:34px;background:var(--band);color:var(--on-band);font-size:9px;line-height:13px;text-align:center;padding-top:4px}

/* Business card back */
.card-back{left:802px;top:615px;background:var(--band)}
.card-back .mark{position:absolute;left:153px;top:49px;width:70px;height:70px;background:var(--on-band)}
.card-back .brand{left:0;width:100%;top:129px;text-align:center;color:var(--on-band);font-size:21px}
</style>
</head>
<body>

<section class="sheet letterhead">
  <div class="mark" aria-hidden="true"></div>
  <div class="brand">GREYMARSH<span class="line2">CONTRACTS</span></div>
  <ul class="contact">
    <li><svg class="icon" viewBox="0 0 24 24"><path d="M5 3h4l2 5-3 2a11 11 0 0 0 6 6l2-3 5 2v4a2 2 0 0 1-2 2A17 17 0 0 1 3 5a2 2 0 0 1 2-2z"/></svg>+91-22-28754193</li>
    <li><svg class="icon" viewBox="0 0 24 24"><rect x="2" y="5" width="20" height="14"/><path d="M2 5l10 8 10-8"/></svg>kelvanjoshi@mailbrook.example</li>
    <li><svg class="icon" viewBox="0 0 24 24"><circle cx="12" cy="12" r="10"/><path d="M2 12h20M12 2c3 3 3 17 0 20M12 2c-3 3-3 17 0 20"/></svg>www.greymarshcontracts.example</li>
  </ul>
  <div class="watermark" aria-hidden="true"></div>
  <footer class="footer">
    Greymarsh Engineering Contracts LLP: Block No.317, Wing C, Tulvo Trade Court, Manek Pural Road<br>
    Ruparel Industrial Estate, Goregaon(E), Mumbai - 400 063
  </footer>
</section>

<section class="card card-front">
  <div class="mark" aria-hidden="true"></div>
  <div class="brand">GREYMARSH<span class="line2">CONTRACTS</span></div>
  <div class="divider"></div>
  <div class="person">
    <div class="name">Kelvan Joshi</div>
    <div class="role">Designated Partner</div>
    <ul class="contact">
      <li><svg class="icon" viewBox="0 0 24 24"><path d="M5 3h4l2 5-3 2a11 11 0 0 0 6 6l2-3 5 2v4a2 2 0 0 1-2 2A17 17 0 0 1 3 5a2 2 0 0 1 2-2z"/></svg>+91 97415 60382</li>
      <li><svg class="icon" viewBox="0 0 24 24"><rect x="2" y="5" width="20" height="14"/><path d="M2 5l10 8 10-8"/></svg>kelvanjoshi@mailbrook.example</li>
      <li><svg class="icon" viewBox="0 0 24 24"><circle cx="12" cy="12" r="10"/><path d="M2 12h20M12 2c3 3 3 17 0 20M12 2c-3 3-3 17 0 20"/></svg>www.greymarshcontracts.example</li>
    </ul>
  </div>
  <footer class="footer">
    Greymarsh Engineering Contracts LLP: Block No.317, Wing C, Tulvo Trade Court<br>
    Manek Pural Road, Ruparel Industrial Estate, Goregaon(E), Mumbai - 400 063
  </footer>
</section>

<section class="card card-back">
  <div class="mark" aria-hidden="true"></div>
  <div class="brand">GREYMARSH<span class="line2">CONTRACTS</span></div>
</section>

</body>
</html>
```